RWT Fittings Ltd Business Cards

We need a business card with our business logo. We provide window and door installations on high-rises in west coast British Colombia, Canada.

I would like my business information and details on one side of the card, and the other side the company name with logo

Target Market(s)

General Contractors

Industry/Entity Type

Construction

Contact Information for Business Card

one side i want my company name and logo in the dark theme logo that i provided

Requirements
Must have
• Marco Peltieri, 16045518293, RWTFittings@mailbox-demo.com, 1407-5194 Linden Row Burnaby BC, V5H 2K9, Owner & Manager

```html
<!DOCTYPE html>
<html lang="en">
<head>
<meta charset="utf-8">
<title>RWT Fittings Ltd — Business Card</title>
<link rel="stylesheet" href="https://fonts.googleapis.com/css2?family=Tenor+Sans&display=swap">
<style>
  :root {
    --page-bg: #e6e3de;
    --navy-light: #22364f;
    --navy-dark: #0e1b2b;
    --cyan: #3fd2ea;
    --slate: #8a949e;
    --brand-blue: #1f8cc8;
    --taupe: #736a66;
    --ink: #4a4a4a;
    --divider: #b9b9b9;
    --card-white: #fbfbfb;
  }
  * { margin: 0; padding: 0; box-sizing: border-box; }
  html, body {
    width: 1200px; height: 900px; overflow: hidden;
    background: var(--page-bg);
    font-family: "Tenor Sans", sans-serif;
  }
  .canvas { position: relative; width: 1200px; height: 900px; }
  .card {
    position: absolute; left: 330px; width: 540px; height: 310px;
    border-radius: 26px;
    box-shadow: 0 10px 30px rgba(0,0,0,.18);
    overflow: hidden;
  }
  .card--front {
    top: 110px;
    background: radial-gradient(ellipse at 45% 45%, var(--navy-light), var(--navy-dark) 80%);
    display: flex; align-items: center; justify-content: center;
  }
  .card--back { top: 480px; background: var(--card-white); }

  .wordmark { display: flex; align-items: center; gap: 14px; }
  .wordmark__square { width: 34px; height: 34px; background: var(--slate); }
  .wordmark__name { font-size: 34px; letter-spacing: 1px; white-space: nowrap; }
  .card--front .wordmark__name { color: var(--cyan); }

  .card--back .wordmark { position: absolute; left: 28px; top: 34px; gap: 10px; }
  .card--back .wordmark__square { width: 26px; height: 26px; background: var(--taupe); }
  .card--back .wordmark__name { color: var(--brand-blue); font-size: 27px; }

  .contact-block {
    position: absolute; right: 30px; bottom: 40px;
    display: flex; align-items: stretch;
  }
  .person { text-align: right; padding-right: 14px; display: flex; flex-direction: column; justify-content: flex-end; }
  .person__title { color: var(--ink); font-size: 15px; }
  .person__name { color: var(--brand-blue); font-size: 17px; letter-spacing: .5px; }
  .contact-list { list-style: none; border-left: 1px solid var(--divider); padding-left: 12px; }
  .contact-list li { display: flex; align-items: flex-start; gap: 7px; color: var(--ink); font-size: 13px; line-height: 19px; }
  .contact-list svg { width: 13px; height: 13px; margin-top: 3px; flex: none; fill: var(--brand-blue); }
</style>
</head>
<body>
<main class="canvas">
  <section class="card card--front" aria-label="Card front">
    <div class="wordmark">
      <span class="wordmark__square"></span>
      <span class="wordmark__name">RWT Fittings Ltd</span>
    </div>
  </section>

  <section class="card card--back" aria-label="Card back">
    <div class="wordmark">
      <span class="wordmark__square"></span>
      <span class="wordmark__name">RWT Fittings Ltd</span>
    </div>

    <div class="contact-block">
      <div class="person">
        <span class="person__title">CEO</span>
        <span class="person__name">MARCO PELTIERI</span>
      </div>
      <ul class="contact-list">
        <li>
          <svg viewBox="0 0 24 24" aria-hidden="true"><path d="M6.6 10.8a15 15 0 0 0 6.6 6.6l2.2-2.2a1 1 0 0 1 1-.25 11.4 11.4 0 0 0 3.6.6 1 1 0 0 1 1 1V20a1 1 0 0 1-1 1A17 17 0 0 1 3 4a1 1 0 0 1 1-1h3.5a1 1 0 0 1 1 1c0 1.25.2 2.45.6 3.6a1 1 0 0 1-.25 1z"/></svg>
          <span>1-604-551-8293</span>
        </li>
        <li>
          <svg viewBox="0 0 24 24" aria-hidden="true"><path d="M2 5h20v14H2zm2 2v.5l8 5 8-5V7l-8 5z"/></svg>
          <span>RWTFittings@mailbox-demo.com</span>
        </li>
        <li>
          <svg viewBox="0 0 24 24" aria-hidden="true"><path d="M12 2a7 7 0 0 0-7 7c0 5 7 13 7 13s7-8 7-13a7 7 0 0 0-7-7zm0 9.5A2.5 2.5 0 1 1 12 6.5a2.5 2.5 0 0 1 0 5z"/></svg>
          <span>1407-5194 Linden Row<br>Burnaby BC, V5H 2K9</span>
        </li>
      </ul>
    </div>
  </section>
</main>
</body>
</html>
```